Business Card for Coastal Tundrabridge Advisory

We need a business card for Coastal Tundrabridge Advisory. The company website address is provided below. The company logo is attached. We provide specialized permafrost services to the mining, transportation, and oil & gas industries. The card should be prepared for:
Matthias Korhonen, PhD.
Coastal Tundrabridge Advisory
PO Box 418259
Quillwater, Alaska 99642
Direct: +1-907-555-0143
Email: mkorhonen@tundrabridgeadvisory.example
Website: www.coastaltundrabridgeadvisory.example

```html
<!DOCTYPE html>
<html lang="en">
<head>
<meta charset="utf-8">
<title>Coastal Tundrabridge Advisory – Business Card</title>
<link rel="stylesheet" href="https://fonts.googleapis.com/css2?family=Open+Sans:ital,wght@0,600;1,700&family=Roboto+Condensed:wght@400&display=swap">
<style>
  :root {
    --page: #efefef;
    --charcoal: #333333;
    --glacier: #1fa0c0;
    --white: #ffffff;
    --ink: #111111;
  }
  * { margin: 0; padding: 0; box-sizing: border-box; }
  html, body { width: 1200px; height: 1200px; overflow: hidden; }
  body { background: var(--page); position: relative; }

  .card {
    position: absolute;
    left: 236px;
    width: 727px;
    height: 413px;
    border-radius: 34px;
    overflow: hidden;
  }
  .card--front { top: 155px; background: var(--glacier); }
  .card--back  { top: 651px; background: var(--charcoal); }

  .card__shapes { position: absolute; inset: 0; width: 100%; height: 100%; }

  .identity {
    position: absolute;
    right: calc(727px - 283px);
    top: 178px;
    text-align: right;
    color: var(--white);
  }
  .identity__name {
    font-family: "Open Sans", sans-serif;
    font-style: italic;
    font-weight: 700;
    font-size: 19px;
    line-height: 26px;
    letter-spacing: -0.3px;
  }
  .identity__role {
    font-family: "Roboto Condensed", sans-serif;
    font-size: 15px;
    line-height: 20px;
  }

  .contact-list {
    position: absolute;
    left: 342px;
    top: 152px;
    list-style: none;
    font-family: "Roboto Condensed", sans-serif;
    font-size: 15px;
    color: var(--white);
  }
  .contact-list__item {
    display: flex;
    align-items: center;
    height: 28px;
  }
  .contact-list__icon { width: 22px; height: 22px; margin-right: 10px; flex: none; }

  .mailing-address {
    position: absolute;
    left: 374px;
    top: 335px;
    font-family: "Roboto Condensed", sans-serif;
    font-size: 15px;
    line-height: 23px;
    color: var(--white);
  }

  .company-name {
    position: absolute;
    left: 0; right: 0;
    top: 190px;
    text-align: center;
    font-family: "Open Sans", sans-serif;
    font-weight: 600;
    font-size: 24px;
    letter-spacing: 5px;
    text-transform: uppercase;
    color: var(--ink);
  }
</style>
</head>
<body>

  <section class="card card--front" aria-label="Business card front">
    <svg class="card__shapes" viewBox="0 0 727 413" aria-hidden="true">
      <path fill="var(--charcoal)" d="M0 0 H205 C290 50 340 130 326 215 C316 290 292 355 256 413 H0 Z"/>
      <path fill="var(--charcoal)" d="M727 128 H682 Q672 128 666 138 L658 200 Q655 205 658 210 L666 273 Q672 283 682 283 H727 Z"/>
    </svg>

    <div class="identity">
      <p class="identity__name">Matthias Korhonen, PhD</p>
      <p class="identity__role">Founder &amp; Director</p>
    </div>

    <ul class="contact-list">
      <li class="contact-list__item">
        <svg class="contact-list__icon" viewBox="0 0 22 22" aria-hidden="true">
          <circle cx="11" cy="11" r="10" fill="var(--white)"/>
          <path fill="var(--glacier)" d="M7 6 L9 6 L10 9 L8.7 10 Q10 12.5 12 13.3 L13 12 L16 13 L16 15 Q15 16.5 13 16 Q8 14 6 9 Q5.5 7 7 6 Z"/>
        </svg>
        <span>+1-907-555-0143</span>
      </li>
      <li class="contact-list__item">
        <svg class="contact-list__icon" viewBox="0 0 22 22" aria-hidden="true">
          <circle cx="11" cy="11" r="10" fill="var(--white)"/>
          <rect x="7.5" y="5" width="7" height="12" rx="1.2" fill="none" stroke="var(--glacier)" stroke-width="1.4"/>
          <circle cx="11" cy="15" r="0.8" fill="var(--glacier)"/>
        </svg>
        <span>(907) 555 0143</span>
      </li>
      <li class="contact-list__item">
        <svg class="contact-list__icon" viewBox="0 0 22 22" aria-hidden="true">
          <circle cx="11" cy="11" r="10" fill="var(--white)"/>
          <rect x="6" y="7.5" width="10" height="7" fill="var(--glacier)"/>
          <path d="M6 7.5 L11 11.5 L16 7.5" fill="none" stroke="var(--white)" stroke-width="1"/>
        </svg>
        <span>mkorhonen@tundrabridgeadvisory.example</span>
      </li>
      <li class="contact-list__item">
        <svg class="contact-list__icon" viewBox="0 0 22 22" aria-hidden="true">
          <circle cx="11" cy="11" r="10" fill="var(--white)"/>
          <circle cx="11" cy="11" r="5.5" fill="none" stroke="var(--glacier)" stroke-width="1.3"/>
          <path d="M5.5 11 H16.5 M11 5.5 Q8 11 11 16.5 Q14 11 11 5.5" fill="none" stroke="var(--glacier)" stroke-width="1.1"/>
        </svg>
        <span>www.coastaltundrabridgeadvisory.example</span>
      </li>
    </ul>

    <address class="mailing-address" style="font-style: normal;">
      PO Box 418259<br>
      Quillwater, Alaska 99642
    </address>
  </section>

  <section class="card card--back" aria-label="Business card back">
    <p class="company-name">Coastal Tundrabridge Advisory</p>
  </section>

</body>
</html>
```